Brightmere plain square mark Design

Build out a really nice and professional plain square mark Page and full banner for Brightmere perhaps with the our services portfolio across the page as well,
Pls check www.brightmere-example.com.au for ideas to a make the plain square mark Page look professional like a similar theme to our website and the porfolio of services

Main photo please emphasis the equipment cleaning and the gurney cleaning a lower priority to emphasize is the general cleaning
Thanks very much

Target Market(s)

Restaurant, warehouses, factories, car and fleet companies, hotels and buffets, chain restaurants, pizza huts, burger eateries, leisure centres

Industry/Entity Type

Cleaning Services

Font styles to use
Serif

Colors
3277b5
f04a50
f37122
fcf299
ec1f27

Requirements
Must have
• Energy and professional plain square mark Site with some of the Brightmere Flowers across it and the portfolio of services
Nice to have
• Good vibrant colours

Professional similar to the website

```html
<!DOCTYPE html>
<html lang="en">
<head>
<meta charset="utf-8">
<title>Brightmere Social Page Layout</title>
<link rel="stylesheet" href="https://fonts.googleapis.com/css2?family=Source+Sans+3:wght@400;600&family=Crimson+Text:wght@400;600&display=swap">
<style>
:root{
  --bar:#4b5b9c;
  --page:#e9ebee;
  --card:#ffffff;
  --line:#dddfe2;
  --label:#1a9ad6;
  --ink:#1c1e21;
  --muted:#777a80;
  --link:#3277b5;
  --brand:#f04a50;
  --orange:#f37122;
  --red:#ec1f27;
  --cream:#fcf299;
}
*{box-sizing:border-box;margin:0;padding:0}
html,body{width:1200px;height:2730px;overflow:hidden}
body{position:relative;background:var(--page);font-family:"Source Sans 3",Arial,sans-serif;color:var(--ink)}
.abs{position:absolute}
.topbar{left:0;top:0;width:1200px;height:57px;background:var(--bar)}
.topbar .mark{left:104px;top:14px;width:31px;height:31px;background:#fff;border-radius:4px;opacity:.9}
.topbar .search{left:202px;top:15px;width:351px;height:29px;background:#fff;border-radius:3px}
.topbar .avatar{left:603px;top:16px;width:29px;height:29px;border-radius:50%;background:#f37122}
.topbar .user,.topbar .home{top:19px;color:#fff;font-size:15px}
.topbar .icon{top:19px;width:20px;height:20px;border-radius:50%;background:#2d3a6d}
.tag{background:var(--label);color:#fff;font-size:19px;line-height:1.2;display:flex;align-items:center;justify-content:center;text-align:center}
.profile-circle{left:27px;top:80px;width:182px;height:182px;border-radius:50%;background:#fff;box-shadow:0 3px 8px rgba(0,0,0,.25);display:flex;align-items:center;justify-content:center;gap:7px}
.brand{color:var(--brand);font-family:"Crimson Text",Georgia,serif;font-weight:600}
.dot{border-radius:50%;background:var(--link);display:inline-block}
.page-name{left:42px;top:316px;font-size:25px}
.handle{left:42px;top:352px;font-size:14px}
.nav-bar{left:42px;width:129px;height:10px;background:#d8dadf}
.photo{background:linear-gradient(120deg,#3a2f25 0%,#8a7d6e 35%,#cfc8be 55%,#2b2a2a 75%,#6d6a63 100%)}
.strip{left:228px;top:421px;width:929px;height:49px;background:#fff;border-top:1px solid var(--line)}
.btn{top:434px;height:29px;border:1px solid #c9ccd3;border-radius:3px;background:#f5f6f7;font-size:12px;display:flex;align-items:center;padding:0 8px;gap:5px;color:#4b4f56}
.panel{background:#fafafa;box-shadow:0 0 6px rgba(0,0,0,.12)}
.panel-title{font-size:16px}
.post{background:var(--card);border:2px solid #ececec}
.post-head{display:flex;align-items:center;gap:10px}
.mini-logo{font-size:8px;color:var(--brand);font-family:"Crimson Text",serif;display:flex;align-items:center;gap:2px}
.post-name{font-size:22px}
.post-time{font-size:16px;color:var(--muted)}
.body-text{font-size:14px;line-height:19.4px;letter-spacing:-.2px}
.body-text p{margin-bottom:19px}
.hash{color:var(--link)}
.tile{background:var(--cream);display:flex;align-items:center;justify-content:center;font-family:"Crimson Text",serif;font-size:24px;font-weight:600;color:var(--red)}
.reacts{display:flex;align-items:center;justify-content:space-between;font-size:18px}
.reacts .faces{display:flex;align-items:center;gap:4px}
.r-like{width:19px;height:19px;border-radius:50%;background:var(--link)}
.r-love{width:19px;height:19px;border-radius:50%;background:var(--red);margin-left:-6px}
.action{display:flex;align-items:center;gap:8px;font-size:19px;color:var(--muted)}
.divider{height:2px;background:#ececec}
.caption{background:rgba(255,255,255,.55);font-family:"Crimson Text",serif;font-size:16px;line-height:19px;color:var(--orange);padding:10px 44px}
.info-row{display:flex;align-items:center;gap:16px;font-size:15px}
.info-row svg{width:18px;height:18px;flex:none}
</style>
</head>
<body>

<header class="abs topbar">
  <div class="abs mark"></div>
  <div class="abs search"></div>
  <div class="abs avatar"></div>
  <span class="abs user" style="left:646px">alex</span>
  <span class="abs home" style="left:742px">Home</span>
  <span class="abs icon" style="left:833px"></span>
  <span class="abs icon" style="left:877px"></span>
  <span class="abs icon" style="left:918px"></span>
  <span class="abs icon" style="left:963px"></span>
</header>

<div class="abs tag" style="left:32px;top:50px;width:164px;height:32px">PROFILE PHOTO</div>
<div class="abs tag" style="left:940px;top:48px;width:194px;height:30px">COVER PHOTO</div>

<div class="abs profile-circle"><span class="dot" style="width:18px;height:18px"></span><span class="brand" style="font-size:23px">Brightmere</span></div>
<div class="abs page-name">Brightmere</div>
<div class="abs handle">@Brightmere</div>
<div class="abs nav-bar" style="top:417px"></div>
<div class="abs nav-bar" style="top:447px"></div>
<div class="abs nav-bar" style="top:478px"></div>
<div class="abs nav-bar" style="top:508px"></div>

<div class="abs photo" role="img" aria-label="Commercial kitchen equipment being cleaned" style="left:228px;top:80px;width:929px;height:341px"></div>
<div class="abs strip"></div>
<div class="abs btn" style="left:249px">Like</div>
<div class="abs btn" style="left:329px;border-radius:3px 0 0 3px">+ Follow</div>
<div class="abs btn" style="left:394px;border-radius:0">Message</div>
<div class="abs btn" style="left:491px;width:52px;justify-content:center;font-weight:600;letter-spacing:2px">•••</div>

<div class="abs tag" style="left:823px;top:455px;width:185px;height:33px">ABOUT US SECTION</div>
<div class="abs tag" style="left:78px;top:597px;width:150px;height:35px">PUBLICATIONS</div>

<!-- Publication 1 -->
<section class="abs panel" style="left:228px;top:491px;width:550px;height:837px">
  <div class="abs panel-title" style="left:20px;top:8px;font-size:14px">Publications</div>
  <article class="abs post" style="left:15px;top:40px;width:513px;height:780px">
    <div class="abs post-head" style="left:24px;top:30px"><span class="mini-logo"><span class="dot" style="width:7px;height:7px"></span>Brightmere</span><span class="post-name">Brightmere</span></div>
    <div class="abs post-time" style="left:86px;top:66px">13 hours ago &nbsp;•</div>
    <div class="abs body-text" style="left:22px;top:108px;width:470px">
      <p>OUR PURPOSE. Is to provide high quality hygiene and sanitisation services to each of our dedicated portfolios across equipment cleaning services, gurney and playground cleaning, general commercial cleaning and property facility maintenance services to create the most effective results for our customers and community. <span class="hash">#Brightmere #Safety&amp;Environment</span></p>
      <p>OUR VISION. Sustainable commercial environment and food service equipment cleaning and sanitisation service provider. Recognised as being the most effective brand, growing employees and giving back to the community for generations to come. <span class="hash">#Brightmere #Safety&amp;Environment</span></p>
      <p>OUR STRATEGY. To differentiate ourselves through a prevailing focus on customer service, in everything we do and every interaction we have to be a positive and professional experience. We treat our people as skilled cleaning professionals who are the foundation of our companys sustainability. <span class="hash">#Brightmere #Safety&amp;Environment</span></p>
    </div>
    <div class="abs tile" style="left:0;top:444px;width:167px;height:170px">Our Purpose</div>
    <div class="abs tile" style="left:172px;top:444px;width:167px;height:170px">Our Vision</div>
    <div class="abs tile" style="left:345px;top:444px;width:167px;height:170px">Our Strategy</div>
    <div class="abs reacts" style="left:4px;top:658px;width:500px"><span class="faces"><span class="r-like"></span><span class="r-love"></span>&nbsp;Your Friend and 74 others</span><span>15 Comments</span></div>
    <div class="abs divider" style="left:0;top:698px;width:513px"></div>
    <div class="abs action" style="left:82px;top:720px"><svg width="28" height="28" viewBox="0 0 24 24" fill="none" stroke="#777a80" stroke-width="1.5"><path d="M7 10v11H3V10zM7 10l4-8c2 0 3 1 2.5 3L13 9h6c1.5 0 2.5 1.3 2 2.8l-2 7.4c-.3 1.1-1.2 1.8-2.3 1.8H7"/></svg>Like</div>
    <div class="abs action" style="left:335px;top:718px"><svg width="28" height="28" viewBox="0 0 24 24" fill="none" stroke="#777a80" stroke-width="1.5"><path d="M3 4h18v12H10l-5 4v-4H3z"/></svg>Comment</div>
  </article>
</section>

<!-- About -->
<section class="abs panel" style="left:795px;top:491px;width:362px;height:312px;background:#fff;overflow:hidden">
  <div class="abs" style="left:30px;top:52px;display:flex;align-items:center;gap:6px"><span class="dot" style="width:18px;height:18px"></span><span class="brand" style="font-size:22px">Brightmere</span></div>
  <div class="abs" style="left:51px;top:130px;font-size:15px">About Ous</div>
  <div class="abs" style="left:38px;top:182px;font-size:14px;letter-spacing:-.3px">WE HAVE BEEN IN BUSINESS FOR 15 YEARS.</div>
  <div class="abs" style="left:41px;top:219px;width:274px;font-size:14px;line-height:19px;text-align:justify;letter-spacing:-.2px">We have been in the Commercial Cleaning and Maintenance business for 15 years. We have built a strong and steady reputation. Our people are professional, reliable and</div>
</section>

<!-- Information -->
<section class="abs panel" style="left:795px;top:822px;width:362px;height:272px;background:#fff">
  <div class="abs" style="left:30px;top:35px;font-size:15px">Information</div>
  <div class="abs info-row" style="left:32px;top:81px"><svg viewBox="0 0 24 24" fill="none" stroke="#666" stroke-width="1.5"><path d="M5 3l4 1 1 5-2 1c1 3 3 5 6 6l1-2 5 1 1 4c-8 1-16-7-16-16z"/></svg>+1300 555 019</div>
  <div class="abs info-row" style="left:32px;top:110px"><svg viewBox="0 0 24 24" fill="none" stroke="#666" stroke-width="1.5"><circle cx="12" cy="12" r="8"/></svg></div>
  <div class="abs info-row" style="left:32px;top:154px"><svg viewBox="0 0 24 24" fill="none" stroke="#666" stroke-width="1.5"><circle cx="12" cy="12" r="8"/><path d="M4 12h16M12 4c3 3 3 13 0 16M12 4c-3 3-3 13 0 16"/></svg>www.brightmere-example.com.au</div>
  <div class="abs info-row" style="left:32px;top:181px"><svg viewBox="0 0 24 24" fill="none" stroke="#666" stroke-width="1.5"><path d="M3 6h18v13H3zM3 10h18"/></svg>Service Company</div>
  <div class="abs info-row" style="left:32px;top:207px"><svg viewBox="0 0 24 24" fill="none" stroke="#666" stroke-width="1.5"><path d="M4 20l1-4L16 5l3 3L8 19z"/></svg>service@brightmere-example.com.au</div>
</section>
<div class="abs tag" style="left:905px;top:1095px;width:217px;height:34px">INFORMATION SECTION</div>

<div class="abs tag" style="left:78px;top:1646px;width:150px;height:36px">PUBLICATIONS</div>

<!-- Publication 2 -->
<section class="abs panel" style="left:228px;top:1343px;width:550px;height:860px">
  <div class="abs panel-title" style="left:29px;top:16px">Publications</div>
  <article class="abs post" style="left:15px;top:50px;width:516px;height:788px">
    <div class="abs post-head" style="left:20px;top:22px"><span class="mini-logo"><span class="dot" style="width:7px;height:7px"></span>Brightmere</span><span class="post-name">Brightmere</span></div>
    <div class="abs post-time" style="left:83px;top:58px">13 hours ago &nbsp;•</div>
    <div class="abs" style="left:18px;top:95px;font-size:15px;letter-spacing:-.3px">Our Services. <span class="hash">#Brightmere #Safety&amp;Environment</span></div>

    <div class="abs photo" role="img" aria-label="Equipment cleaning and sanitisation" style="left:0;top:136px;width:256px;height:256px;background:linear-gradient(160deg,#1c3550,#5b7fa3 50%,#2b4d72)"></div>
    <div class="abs caption" style="left:0;top:219px;width:256px">Equipment Cleaning<br>&amp; Sanitisation</div>
    <div class="abs photo" role="img" aria-label="Kitchen detail cleaning" style="left:259px;top:136px;width:257px;height:256px;background:linear-gradient(160deg,#e8e8e8,#9a9da2 50%,#3a3a3a)"></div>
    <div class="abs caption" style="left:259px;top:219px;width:257px">Kitchen Detail<br>Cleaning</div>
    <div class="abs photo" role="img" aria-label="High pressure gurney cleaning of playground equipment" style="left:0;top:396px;width:256px;height:256px;background:linear-gradient(170deg,#6c5a3a,#8a8f63 40%,#c8c3b8 70%,#6b6760)"></div>
    <div class="abs caption" style="left:0;top:477px;width:256px">High Pressure Gurney &amp;<br>Play Ground Equipment</div>
    <div class="abs photo" role="img" aria-label="General cleaning and facility maintenance" style="left:259px;top:396px;width:257px;height:256px;background:linear-gradient(170deg,#eef3f7,#cdd9e3 60%,#8aa0b4)"></div>
    <div class="abs caption" style="left:259px;top:477px;width:257px">General Cleaning<br>&amp; &nbsp;Facility Maintenance</div>

    <div class="abs reacts" style="left:16px;top:676px;width:476px"><span class="faces"><span class="r-like"></span><span class="r-love"></span>&nbsp;Your Friend and 74 others</span><span>15 Comments</span></div>
    <div class="abs divider" style="left:16px;top:714px;width:476px"></div>
    <div class="abs action" style="left:92px;top:738px"><svg width="28" height="28" viewBox="0 0 24 24" fill="none" stroke="#777a80" stroke-width="1.5"><path d="M7 10v11H3V10zM7 10l4-8c2 0 3 1 2.5 3L13 9h6c1.5 0 2.5 1.3 2 2.8l-2 7.4c-.3 1.1-1.2 1.8-2.3 1.8H7"/></svg>Like</div>
    <div class="abs action" style="left:334px;top:740px;font-size:17px"><svg width="28" height="28" viewBox="0 0 24 24" fill="none" stroke="#777a80" stroke-width="1.5"><path d="M3 4h18v12H10l-5 4v-4H3z"/></svg>Comment</div>
  </article>
</section>

<div class="abs tag" style="left:48px;top:2266px;width:177px;height:61px;font-size:17px;text-align:left;justify-content:flex-start;padding-left:10px">SUMMARY<br>PUBLISHED PHOTOS</div>

<!-- Photos -->
<section class="abs panel" style="left:228px;top:2222px;width:547px;height:520px">
  <div class="abs panel-title" style="left:27px;top:28px">Photos</div>
  <div class="abs photo" role="img" aria-label="Commercial kitchen equipment being cleaned" style="left:13px;top:63px;width:515px;height:253px"></div>
  <div class="abs photo" role="img" aria-label="High pressure gurney cleaning of playground equipment" style="left:13px;top:322px;width:256px;height:200px;background:linear-gradient(170deg,#6c5a3a,#8a8f63 40%,#c8c3b8 70%,#6b6760)"></div>
  <div class="abs caption" style="left:13px;top:409px;width:256px">High Pressure Gurney &amp;<br>Play Ground Equipment</div>
  <div class="abs photo" role="img" aria-label="General cleaning and facility maintenance" style="left:273px;top:322px;width:255px;height:200px;background:linear-gradient(170deg,#eef3f7,#cdd9e3 60%,#8aa0b4)"></div>
  <div class="abs caption" style="left:273px;top:409px;width:255px">General Cleaning<br>&amp; &nbsp;Facility Maintenance</div>
</section>

</body>
</html>
```